business card deign

Logo needs the following on it.
1. attached logo
2. Tagline - "If it keeps a drink cold or the party going...we do it!"
3. Name- Dalton Pikes, Founder and CPO
4. Address - 412 E. Carver Avenue, Ste 2207, Tampa, FL. 33917
5. Phone - 555.318.4726

```html
<!DOCTYPE html>
<html lang="en">
<head>
<meta charset="UTF-8">
<title>Northgate Supply Business Card</title>
<link href="https://fonts.googleapis.com/css2?family=Montserrat:wght@400;500;600;800&display=swap" rel="stylesheet">
<style>
  :root {
    --page-bg: #e6e6e4;
    --card-bg: #ffffff;
    --ink: #111111;
    --ink-soft: #222222;
    --card-shadow: rgba(0, 0, 0, 0.16);
  }
  * { box-sizing: border-box; margin: 0; padding: 0; }
  html, body {
    width: 1200px;
    height: 900px;
    overflow: hidden;
    background: var(--page-bg);
    font-family: "Montserrat", sans-serif;
    color: var(--ink);
  }
  .canvas {
    width: 1200px;
    height: 900px;
    display: flex;
    flex-direction: column;
    align-items: center;
    justify-content: center;
    gap: 44px;
  }
  .card {
    width: 660px;
    height: 378px;
    background: var(--card-bg);
    border-radius: 22px;
    box-shadow: 0 10px 30px var(--card-shadow);
    position: relative;
  }
  .brand {
    display: flex;
    align-items: center;
    gap: 12px;
  }
  .brand-square {
    flex: none;
    width: 16px;
    height: 16px;
    background: var(--ink);
  }
  .brand-name {
    font-weight: 600;
    letter-spacing: 0;
    white-space: nowrap;
    color: var(--ink);
  }
  /* Front */
  .card-front {
    display: flex;
    align-items: center;
    justify-content: center;
  }
  .card-front .brand-name { font-size: 40px; }
  .card-front .brand-square { width: 22px; height: 22px; }
  /* Back */
  .card-back-body {
    position: absolute;
    top: 78px;
    left: 0;
    right: 0;
    display: flex;
    align-items: center;
    justify-content: center;
    gap: 28px;
  }
  .card-back .brand { width: 240px; justify-content: flex-end; }
  .card-back .brand-name { font-size: 24px; }
  .divider {
    flex: none;
    width: 2px;
    height: 178px;
    background: var(--ink);
  }
  .contact { width: 250px; }
  .contact-name {
    font-weight: 800;
    font-size: 19px;
    letter-spacing: 0.04em;
    text-transform: uppercase;
  }
  .contact-title {
    font-weight: 500;
    font-size: 16px;
    letter-spacing: 0.05em;
    color: var(--ink-soft);
    margin-top: 2px;
  }
  .contact-list {
    list-style: none;
    margin-top: 20px;
    font-size: 15px;
    font-weight: 500;
    line-height: 1.35;
  }
  .contact-list li {
    display: flex;
    gap: 10px;
    align-items: flex-start;
  }
  .contact-list svg {
    width: 16px;
    height: 16px;
    flex: none;
    margin-top: 2px;
    fill: var(--ink);
  }
  .tagline {
    position: absolute;
    bottom: 42px;
    left: 0;
    right: 0;
    text-align: center;
    font-size: 16px;
    font-weight: 500;
    letter-spacing: 0.02em;
  }
</style>
</head>
<body>
<main class="canvas">
  <section class="card card-front">
    <div class="brand">
      <span class="brand-square"></span>
      <span class="brand-name">Northgate Supply</span>
    </div>
  </section>

  <section class="card card-back">
    <div class="card-back-body">
      <div class="brand">
        <span class="brand-square"></span>
        <span class="brand-name">Northgate Supply</span>
      </div>
      <div class="divider"></div>
      <div class="contact">
        <p class="contact-name">Dalton Pikes</p>
        <p class="contact-title">Founder and CPO</p>
        <ul class="contact-list">
          <li>
            <svg viewBox="0 0 24 24" aria-hidden="true"><path d="M3 8c0-2 4-4 9-4s9 2 9 4v2h-5V8H8v2H3z M5 12h14l2 8H3z M12 14a2.5 2.5 0 1 0 0 5a2.5 2.5 0 1 0 0-5z"/></svg>
            <span>555.318.4726</span>
          </li>
          <li>
            <svg viewBox="0 0 24 24" aria-hidden="true"><path d="M12 2a7 7 0 0 0-7 7c0 5 7 13 7 13s7-8 7-13a7 7 0 0 0-7-7zm0 4a3 3 0 1 1 0 6a3 3 0 0 1 0-6z"/></svg>
            <span>412 E. Carver Avenue, Ste 2207, Tampa, FL. 33917</span>
          </li>
        </ul>
      </div>
    </div>
    <p class="tagline">If it keeps a drink cold or the party going...we do it!</p>
  </section>
</main>
</body>
</html>
```